Business Card, A4 Letter Head and DL Envelope for Brandvelle

We are looking for a design for our Business Card, A4 Letter Head and DL Envelope.

Brandvelle is a distributor of promotional products. We specialize in a range of branded promotional products, these include pens, polo shirts, key rings, drink bottles, uniforms and bags to name a few. We are experts in marketing and assist companies in choosing the right promotional product for their needs. We will predominately be an online business where customers visit our website and browse our range of promotional products and branding options.

Our colours are black, red, white and grey.

Files must be supplied in eps, pdf and ai format.

Please display the following information:
Derek Halloway
Account Manager
Suite xxx, 212 Ferrow Lane Melbourne, Victoria 3000
Phone +61 3 5550 1827
Mobile +61 455 016 342
sales@brandvelle-example.com.au
www.brandvelle-example.com.au

```html
<!DOCTYPE html>
<html lang="en">
<head>
<meta charset="utf-8">
<title>Brandvelle – Business Card</title>
<link rel="stylesheet" href="https://fonts.googleapis.com/css2?family=Arimo:wght@400;700&display=swap">
<style>
  :root {
    --ink: #1a1a1a;
    --charcoal: #2b2b2b;
    --brand-red: #d3171d;
    --band-grey: #9e9e9e;
    --muted-grey: #a0a0a0;
    --wordmark-grey: #3c3c3c;
    --paper: #ffffff;
  }
  html, body {
    margin: 0;
    padding: 0;
    width: 1200px;
    height: 733px;
    overflow: hidden;
    background: var(--paper);
  }
  .card {
    position: relative;
    width: 1200px;
    height: 733px;
    background: var(--paper);
    font-family: "Arimo", Arial, sans-serif;
    color: var(--ink);
    overflow: hidden;
  }
  .card-shapes {
    position: absolute;
    inset: 0;
  }
  .brand {
    position: absolute;
    left: 482px;
    top: 95px;
    display: flex;
    align-items: center;
    gap: 20px;
  }
  .brand-dot {
    width: 140px;
    height: 140px;
    border-radius: 50%;
    background: var(--brand-red);
  }
  .brand-name {
    font-size: 62px;
    font-weight: 700;
    letter-spacing: 1px;
    color: var(--wordmark-grey);
    text-transform: uppercase;
    line-height: 1;
  }
  .contact {
    position: absolute;
    left: 84px;
    top: 312px;
  }
  .contact p { margin: 0; }
  .contact-name {
    font-size: 40px;
    line-height: 48px;
  }
  .contact-role {
    font-size: 32px;
    font-weight: 700;
    line-height: 42px;
  }
  .contact-mobile {
    font-size: 38px;
    line-height: 48px;
  }
  .contact-abn {
    margin-top: 12px !important;
    font-size: 34px;
    line-height: 42px;
    color: var(--muted-grey);
  }
  .footer {
    position: absolute;
    left: 74px;
    top: 612px;
    font-size: 35px;
    line-height: 54px;
    color: var(--charcoal);
  }
  .footer p { margin: 0; }
  .footer-line { display: flex; }
  .footer-phone { width: 448px; }
</style>
</head>
<body>
  <div class="card">
    <svg class="card-shapes" width="1200" height="733" viewBox="0 0 1200 733" aria-hidden="true">
      <path class="corner-swoosh" d="M0 0 H605 Q330 40 0 108 Z" fill="var(--charcoal)"/>
      <path class="corner-swoosh-edge" d="M605 0 Q330 40 0 108" fill="none" stroke="var(--brand-red)" stroke-width="6"/>
      <path class="footer-band" d="M0 589 Q720 575 1200 477 V733 H0 Z" fill="var(--band-grey)"/>
    </svg>

    <div class="brand">
      <div class="brand-dot"></div>
      <span class="brand-name">Brandvelle</span>
    </div>

    <div class="contact">
      <p class="contact-name">Derek Halloway</p>
      <p class="contact-role">Account Manager</p>
      <p class="contact-mobile">M: +61 455 016 342</p>
      <p class="contact-abn">ABN&nbsp; 00 000 000 000</p>
    </div>

    <div class="footer">
      <p class="footer-address">Suite xxx, 212 Ferrow Lane Melbourne, Victoria 3000</p>
      <p class="footer-line">
        <span class="footer-phone">T: +61 3 5550 1827</span>
        <span class="footer-email">E: sales@brandvelle-example.com.au</span>
      </p>
    </div>
  </div>
</body>
</html>
```